Email Banner/Facebook post banner

Hi there, we're after a set of sleek Email banners (1200 x 600 px) in jpg and png to use for a HVAC heating and cooling system. We work with Korvo, Tessle, Palvor, Kanemoro and Harukawa HVAC brands and we want to create a series of eDM campaigns.

The messages/headlines are around these: 1. Looking to reduce your gas bills significantly? Harness the efficient power of a HVAC split system to keep your home comfortable all year round! 2. Looking for a powerful heating solution to replace your gas? Access up to $8,000 rebates through the Halden Power Renewal Program! 3. Pay as little as $1,499* for a 3-head split system! Normally $9,900. Available to valued existing customers of Korvane Energy. Hurry!

We want to create at least 5 eDM banner plus 3-4 Facebook post artwork based on the same designs as the eDM. You can just grab images online. We have a design guide too if you can incorporate this. Please quote me a good price.

```html
<!DOCTYPE html>
<html lang="en">
<head>
<meta charset="utf-8">
<title>Korvane Energy – Split System Banner</title>
<link rel="stylesheet" href="https://fonts.googleapis.com/css2?family=Outfit:wght@400;500;600&display=swap">
<style>
  :root {
    --brand-green: #2f7d32;
    --ink: #1f1f1f;
    --wall-light: #efeeee;
    --wall-mid: #e3e2e2;
    --wall-dark: #d6d5d5;
    --unit-white: #f7f7f7;
    --unit-shadow: #cfcfcf;
    --figure-tone: #b9b2ad;
    --faint: rgba(110, 135, 110, 0.14);
    --white: #ffffff;
  }
  * { box-sizing: border-box; margin: 0; padding: 0; }
  html, body { width: 1200px; height: 600px; overflow: hidden; }
  body { font-family: "Outfit", sans-serif; }

  .banner {
    position: relative;
    width: 1200px;
    height: 600px;
    overflow: hidden;
    background: radial-gradient(ellipse at 35% 40%, var(--wall-light) 0%, var(--wall-mid) 55%, var(--wall-dark) 100%);
  }

  .brand {
    position: absolute;
    left: 55px;
    top: 70px;
    display: flex;
    align-items: center;
    gap: 12px;
    color: var(--brand-green);
    font-size: 30px;
    font-weight: 500;
    line-height: 1;
  }
  .brand__mark {
    width: 26px;
    height: 26px;
    background: var(--brand-green);
  }

  .headline {
    position: absolute;
    left: 55px;
    top: 237px;
    color: var(--brand-green);
    font-size: 35px;
    font-weight: 600;
    line-height: 42px;
    white-space: nowrap;
  }
  .subline {
    position: absolute;
    left: 55px;
    top: 337px;
    color: var(--ink);
    font-size: 20.5px;
    font-weight: 500;
    line-height: 29px;
    white-space: nowrap;
  }

  .cta {
    position: absolute;
    left: 48px;
    top: 442px;
    width: 200px;
    height: 65px;
    border-radius: 33px;
    background: var(--brand-green);
    color: var(--white);
    display: flex;
    align-items: center;
    justify-content: center;
    gap: 10px;
    font-size: 22px;
    font-weight: 500;
    text-decoration: none;
  }
  .cta svg { width: 26px; height: 26px; }

  .slider-dots {
    position: absolute;
    left: 81px;
    top: 575px;
    display: flex;
    gap: 8px;
  }
  .slider-dots span {
    width: 9px; height: 9px; border-radius: 50%;
    background: var(--ink);
  }
  .slider-dots .is-active { background: var(--brand-green); }

  .ac-unit {
    position: absolute;
    left: 714px;
    top: 40px;
    width: 464px;
    height: 160px;
    border-radius: 10px 10px 18px 18px;
    background: linear-gradient(180deg, var(--unit-white) 0%, #ececec 80%, var(--unit-shadow) 100%);
  }

  .person {
    position: absolute;
    left: 470px;
    top: 215px;
    width: 410px;
    height: 385px;
    border-radius: 120px 120px 0 0;
    background: linear-gradient(180deg, #8d8580 0%, var(--figure-tone) 60%, #a7a3a3 100%);
  }

  .brand-echo {
    position: absolute;
    left: 945px;
    top: 440px;
    color: var(--faint);
    font-size: 30px;
    font-weight: 500;
    line-height: 1;
  }
</style>
</head>
<body>
  <main class="banner">
    <div class="ac-unit" role="img" aria-label="Photo of a white wall-mounted split system air conditioner"></div>
    <div class="person" role="img" aria-label="Photo of a woman holding an air conditioner remote"></div>

    <div class="brand">
      <span class="brand__mark" aria-hidden="true"></span>
      <span class="brand__name">Korvane Energy</span>
    </div>

    <h1 class="headline">Looking To Reduce Your<br>Gas Bills Significantly?</h1>
    <p class="subline">Harness The Efficient Power of<br>A HVAC Split System To Keep Your<br>Home Comfortable All Year Round</p>

    <a class="cta" href="#contact">
      <svg viewBox="0 0 24 24" fill="none" stroke="currentColor" stroke-width="1.6" stroke-linecap="round" stroke-linejoin="round" aria-hidden="true">
        <path d="M5 3.5h3.2l1.6 4.2-2 1.3a11 11 0 0 0 5.2 5.2l1.3-2 4.2 1.6V17a2 2 0 0 1-2 2A15 15 0 0 1 3 6a2 2 0 0 1 2-2.5z"/>
        <path d="M14.5 3.5a6 6 0 0 1 6 6"/>
        <path d="M14.5 7a2.5 2.5 0 0 1 2.5 2.5"/>
      </svg>
      Contact Us
    </a>

    <div class="slider-dots" aria-hidden="true">
      <span></span><span class="is-active"></span><span></span>
    </div>

    <div class="brand-echo" aria-hidden="true">Korvane Energy</div>
  </main>
</body>
</html>
```